NEW Wordpress Website Design for a Dynamic Long Term Healthcare Company in Hawaii

I would like a new website design for my current company, Marlow Health Collective, which has two different brands - Marlow Homecare and Marlow Senior Living. You can see the current website at www.marlowhealth-example.com. The website should be built using Wordpress Software and the Framewise theme. The website should have a local Hawaii island/tropical feel, but look professional for healthcare. I'm looking for something fresh, and want the designer to select colors, styles, etc.

In the Header, on all pages, I would like a menu that includes Home Care, Senior Living, Rates, and About Us.
Under each of the Header Menu Titles, I would like these drop downs included:
Home Care (drop down pages)- Nurse Aide Care, 24-Hour Home Care, Skilled Nursing, Lifestyle Aide, Hospice at Home, Bathing & Meal Service.
Senior Living (drop down pages) - Long-Term Stay, Short-Term Stay.
Rates (drop down page) - Rates.
About Us (drop down pages) - Our Mission, Ohana Talk, About Dana Marlow.

In the footer, on all pages, you should include the address: 248 Pueo Lane, Suite 310, Honolulu, HI 96817. Phone number: 808-555-0172
The footer should also include buttons for a page called Learn, Caregiver Jobs, and each of the service page links to include: Nurse Aide Care, 24-Hour Home Care, Skilled Nursing, Lifestyle Aide, Hospice at Home, Bathing & Meal Service.
Please don't take the current website and redesign a few aspects. I'm looking for a completely different look and feel.

Target Market(s)

40-80 year olds

Industry/Entity Type

Long Term Healthcare

Coding

Coded - Design and coding required

Requirements
Should not have
• Our existing website as a template. We are looking for a complete redesign. Thank you.

```html
<!DOCTYPE html>
<html lang="en">
<head>
<meta charset="utf-8">
<title>Marlow Health Collective</title>
<link href="https://fonts.googleapis.com/css2?family=Playfair+Display:wght@400;600;700&family=Roboto:wght@400;500;700&display=swap" rel="stylesheet">
<style>
:root{
  --sage:#8fa383;
  --sage-dark:#7d9271;
  --sand:#ddd4c9;
  --sand-light:#e4ddd4;
  --ink:#1e1e1e;
  --muted:#6b6b6b;
  --line:#d8d8d8;
  --footer:#ececec;
  --white:#ffffff;
}
*{margin:0;padding:0;box-sizing:border-box}
html,body{width:1200px;height:3827px;overflow:hidden;background:var(--white)}
body{position:relative;font-family:'Roboto',sans-serif;color:var(--ink)}
.abs{position:absolute}
.serif{font-family:'Playfair Display',serif}

/* top bar */
.topbar{left:686px;top:0;width:514px;height:45px;background:var(--sage);border-bottom-left-radius:22px;color:#fff;font-size:14px;font-weight:500;display:flex;align-items:center;gap:30px;padding-left:30px}
.topbar span{display:flex;align-items:center;gap:10px}
.brand{font-family:'Playfair Display',serif;font-size:26px;font-weight:600;color:var(--sage-dark);display:flex;align-items:center;gap:8px}
.brand i{display:block;width:18px;height:18px;background:var(--sage);border-radius:4px}
.nav{left:496px;top:78px;display:flex;gap:22px;font-size:14px;font-weight:500;letter-spacing:.2px}
.social{top:67px;width:39px;height:39px;border-radius:50%;background:#ebe6df}

/* hero */
.hero{left:0;top:128px;width:1200px;height:500px;overflow:hidden}
.hero-photo{top:0;height:500px;width:600px}
.hero-left{left:0;background:linear-gradient(120deg,#e9ebe2,#c8c3b3 55%,#b6b19e)}
.hero-right{left:600px;background:linear-gradient(240deg,#ede8df,#d9c6a6 55%,#c8a060)}
.hero-word{top:38px;font-family:'Playfair Display',serif;font-weight:700;font-size:54px;color:#9d9d9d;opacity:.85;letter-spacing:1px}
.hero-badge{left:436px;top:97px;width:328px;height:328px;border-radius:50%;background:#fff;box-shadow:0 6px 30px rgba(0,0,0,.12);text-align:center;padding-top:48px}
.hero-badge .welcome{font-size:16px;letter-spacing:.5px}
.hero-badge h1{font-family:'Playfair Display',serif;font-weight:600;font-size:44px;letter-spacing:2px;margin-top:8px}
.hero-badge h2{font-family:'Playfair Display',serif;font-weight:400;font-size:34px;color:#6f6f6f;line-height:46px}

.btn{display:inline-flex;align-items:center;justify-content:center;gap:8px;border-radius:24px;color:#fff;font-size:13px;font-weight:700;letter-spacing:.3px;background:var(--sage)}
.btn.sand{background:var(--sand);color:var(--ink)}
.btn .dot{width:12px;height:12px;border-radius:50%;background:currentColor;position:relative}

/* about */
.about-art{left:193px;top:723px;width:321px;height:354px;border-radius:36px;background:linear-gradient(160deg,#e8e6d9,#d6d3c0)}
.h-section{font-family:'Playfair Display',serif;font-weight:600;font-size:38px}
.para{font-size:14px;line-height:26px;color:var(--muted)}
.rule{width:60px;height:2px;background:var(--sage)}

/* services */
.band{left:0;top:1169px;width:1200px;height:408px;background:var(--sage)}
.card{top:1350px;width:422px;height:548px;background:#fff;box-shadow:0 6px 24px rgba(0,0,0,.1);text-align:center}
.card-photo{position:absolute;left:12px;top:13px;width:398px;height:250px}
.card-icon{position:absolute;left:166px;top:215px;width:90px;height:90px;border-radius:50%;display:flex;align-items:center;justify-content:center}
.card h3{position:absolute;left:0;right:0;top:328px;font-size:26px;font-weight:500}
.card p{position:absolute;left:30px;right:30px;top:372px;font-size:14px;line-height:29px;color:var(--muted)}
.card .btn{position:absolute;left:126px;top:484px;width:169px;height:43px}

/* why */
.feat{width:330px}
.feat h4{font-size:15px;font-weight:700;margin-bottom:8px}
.feat p{font-size:14px;line-height:26px;color:var(--muted)}
.feat.left{text-align:right}
.ficon{width:72px;height:72px;border-radius:50%;display:flex;align-items:center;justify-content:center}

/* cta */
.cta{left:0;top:2536px;width:1200px;height:370px;background:var(--sand-light)}
.cta-photo{left:582px;top:2536px;width:618px;height:370px;background:linear-gradient(90deg,rgba(228,221,212,0),#b9c8cf 40%,#8fb0c0)}

/* form */
.field{height:63px;border:1px solid var(--line);border-radius:32px;box-shadow:0 3px 6px rgba(0,0,0,.08);font-size:14px;color:var(--muted);padding:22px 32px}

/* footer */
.footer{left:0;top:3475px;width:1200px;height:352px;background:var(--footer)}
.fcol h5{font-size:13px;font-weight:700;margin-bottom:14px}
.fcol li{list-style:none;font-size:13px;line-height:25.6px;color:#333}
</style>
</head>
<body>

<div class="abs topbar">
  <span><svg width="14" height="11" viewBox="0 0 14 11"><rect x="0.5" y="0.5" width="13" height="10" rx="1" fill="#fff"/><path d="M1 1l6 5 6-5" stroke="#8fa383" fill="none"/></svg>info@marlowhealth-example.com</span>
  <span><svg width="12" height="12" viewBox="0 0 24 24"><path fill="#fff" d="M6.6 10.8a15 15 0 006.6 6.6l2.2-2.2c.3-.3.7-.4 1-.2 1.1.4 2.3.6 3.6.6.6 0 1 .4 1 1V20c0 .6-.4 1-1 1A17 17 0 013 4c0-.6.4-1 1-1h3.5c.6 0 1 .4 1 1 0 1.3.2 2.5.6 3.6.1.3 0 .7-.2 1z"/></svg>(808) 555-0172</span>
</div>

<div class="abs brand" style="left:111px;top:44px">Marlow</div>
<div class="abs brand" style="left:216px;top:44px;color:#5b8f8a"><i style="background:#9bbab5"></i>Marlow</div>

<nav class="abs nav"><span>HOME CARE</span><span>SENIOR LIVING</span><span>RATES</span><span>ABOUT US</span></nav>
<div class="abs social" style="left:912px"></div>
<div class="abs social" style="left:958px"></div>
<div class="abs social" style="left:1004px"></div>
<div class="abs social" style="left:1050px"></div>

<section class="abs hero">
  <div class="abs hero-photo hero-left" role="img" aria-label="Caregiver chatting with an elderly woman in a bright living room"></div>
  <div class="abs hero-photo hero-right" role="img" aria-label="Smiling senior woman with a young caregiver"></div>
  <div class="abs hero-word" style="left:59px">HOMECARE</div>
  <div class="abs hero-word" style="left:760px">SENIOR LIVING</div>
  <div class="abs hero-badge">
    <div class="welcome">WELCOME TO</div>
    <h1>Marlow</h1>
    <h2>Homecare and<br>Senior Living</h2>
  </div>
  <div class="abs btn" style="left:507px;top:335px;width:186px;height:44px">GET STARTED <span class="dot"></span></div>
  <svg class="abs" style="left:0;bottom:0" width="1200" height="40" viewBox="0 0 1200 40" preserveAspectRatio="none"><path d="M0 30 C200 10 380 40 600 22 S1000 8 1200 26 V40 H0Z" fill="#fff"/></svg>
</section>

<div class="abs about-art" role="img" aria-label="Soft faded photo of a caregiver and senior"></div>
<h2 class="abs h-section" style="left:621px;top:732px">About Us</h2>
<div class="abs rule" style="left:621px;top:780px;width:100px;background:#333"></div>
<p class="abs para" style="left:621px;top:804px;width:390px">At Marlow Health Collective, our mission is to provide compassionate and professional long-term healthcare services that empower individuals to maintain their highest level of independence, health, and well-being in the comfort of their own homes or ours, either through our licensed home healthcare agency - Marlow Homecare, or in our Adult Residential Care Home - Marlow Senior Living.</p>
<div class="abs btn" style="left:621px;top:1011px;width:169px;height:43px">LEARN MORE <span class="dot"></span></div>

<div class="abs band"></div>
<h2 class="abs h-section" style="left:0;width:1200px;text-align:center;top:1248px;color:#fff">What We Do</h2>
<div class="abs rule" style="left:570px;top:1300px;background:#fff"></div>

<div class="abs card" style="left:160px">
  <div class="card-photo" role="img" aria-label="Caregiver serving a meal to a senior couple at home" style="background:linear-gradient(135deg,#7a3e24,#c9a56d 50%,#d9dcb8)"></div>
  <div class="card-icon" style="background:var(--sage)"><svg width="46" height="40" viewBox="0 0 46 40" fill="none" stroke="#fff" stroke-width="2"><path d="M4 20L23 4l19 16M9 16v21h28V16"/><path d="M23 30s-6-4-6-8a3 3 0 016-1 3 3 0 016 1c0 4-6 8-6 8z"/></svg></div>
  <h3>HOMECARE</h3>
  <p>Marlow Homecare understands that every person's care journey is unique. We tailor our in-home services to meet the diverse nurturing experience</p>
  <div class="btn">LEARN MORE <span class="dot"></span></div>
</div>
<div class="abs card" style="left:618px">
  <div class="card-photo" role="img" aria-label="Seniors exercising with an instructor in a sunny lounge" style="background:linear-gradient(135deg,#5d4a33,#c9b58c 50%,#9fae7a)"></div>
  <div class="card-icon" style="background:var(--sand)"><svg width="40" height="40" viewBox="0 0 40 40" fill="none" stroke="#333" stroke-width="2"><circle cx="14" cy="8" r="4"/><circle cx="27" cy="10" r="3.5"/><path d="M8 36V20a6 6 0 0112 0v16M22 36V22a5 5 0 0110 0v14"/></svg></div>
  <h3>SENIOR LIVING</h3>
  <p>Marlow Senior Living creates a warm, supportive, and enriching care home environment where seniors can thrive in their golden years.</p>
  <div class="btn sand">LEARN MORE <span class="dot"></span></div>
</div>

<h2 class="abs h-section" style="left:0;width:1200px;text-align:center;top:1983px">Why Choose Us</h2>
<div class="abs rule" style="left:570px;top:2036px"></div>

<div class="abs" style="left:475px;top:2135px;width:250px;height:250px;border-radius:50%;background:#fff;box-shadow:0 8px 30px rgba(0,0,0,.08)"></div>
<div class="abs" style="left:513px;top:2173px;width:174px;height:174px;border-radius:50%;background:linear-gradient(135deg,#8fa383,#ddd4c9)"></div>

<div class="abs feat left" style="left:75px;top:2084px"><h4>Reduced Burden</h4><p>For families, choosing a senior living facility can alleviate the burden of</p></div>
<div class="abs ficon" style="left:415px;top:2088px;background:var(--sage)"><svg width="30" height="30" viewBox="0 0 30 30" fill="none" stroke="#fff" stroke-width="2"><circle cx="13" cy="13" r="9"/><path d="M20 20l7 7"/></svg></div>
<div class="abs feat left" style="left:22px;top:2221px"><h4>Personalized Care</h4><p>Senior living facilities can tailor care plans to each individual's</p></div>
<div class="abs ficon" style="left:364px;top:2225px;background:var(--sand)"><svg width="32" height="30" viewBox="0 0 32 30" fill="none" stroke="#333" stroke-width="2"><path d="M3 15L16 3l13 12M7 12v16h18V12"/></svg></div>
<div class="abs feat left" style="left:75px;top:2358px"><h4>Peace of Mind</h4><p>Families gain peace of mind knowing that their loved ones are in a secure</p></div>
<div class="abs ficon" style="left:415px;top:2362px;background:var(--sage)"><svg width="28" height="28" viewBox="0 0 28 28" fill="none" stroke="#fff" stroke-width="2"><circle cx="14" cy="14" r="10"/></svg></div>

<div class="abs ficon" style="left:708px;top:2088px;background:var(--sand)"><svg width="30" height="30" viewBox="0 0 30 30" fill="none" stroke="#333" stroke-width="2"><circle cx="15" cy="15" r="10"/><path d="M15 10v10M10 15h10"/></svg></div>
<div class="abs feat" style="left:796px;top:2084px"><h4>Safety and Accessibility</h4><p>Senior living facilities are designed with safety in mind.</p></div>
<div class="abs ficon" style="left:760px;top:2225px;background:var(--sage)"><svg width="32" height="30" viewBox="0 0 32 30" fill="none" stroke="#fff" stroke-width="2"><path d="M3 15L16 3l13 12M7 12v16h18V12M16 16v8M12 20h8"/></svg></div>
<div class="abs feat" style="left:847px;top:2221px"><h4>Healthcare Support</h4><p>Many senior living facilities offer access to healthcare professionals,</p></div>
<div class="abs ficon" style="left:708px;top:2362px;background:var(--sand)"><svg width="32" height="32" viewBox="0 0 32 32" fill="none" stroke="#333" stroke-width="2"><circle cx="9" cy="8" r="3"/><circle cx="23" cy="20" r="3"/><path d="M4 18c0-3 2-5 5-5s5 2 5 5M18 30c0-3 2-5 5-5s5 2 5 5"/></svg></div>
<div class="abs feat" style="left:796px;top:2358px"><h4>Social Interaction</h4><p>Seniors often face social isolation, which can lead to mental</p></div>

<div class="abs cta"></div>
<div class="abs cta-photo" role="img" aria-label="Smiling senior man with a nurse resting a hand on his shoulder"></div>
<h2 class="abs h-section" style="left:111px;top:2616px;font-size:40px">Come See If We're The Right Fit</h2>
<div class="abs rule" style="left:113px;top:2676px"></div>
<p class="abs para" style="left:113px;top:2693px;width:580px">Choosing the right senior living facility involves careful consideration of the individual's needs, preferences, and the available amenities and services.</p>
<div class="abs btn" style="left:113px;top:2771px;width:187px;height:43px">GET STARTED <span class="dot"></span></div>

<h2 class="abs h-section" style="left:0;width:1200px;text-align:center;top:2990px">Get An Appointment</h2>
<div class="abs rule" style="left:570px;top:3043px"></div>
<div class="abs field" style="left:301px;top:3081px;width:292px">Name</div>
<div class="abs field" style="left:607px;top:3081px;width:293px">Email</div>
<div class="abs field" style="left:301px;top:3156px;width:292px">Phone</div>
<div class="abs field" style="left:607px;top:3156px;width:293px">Choose Your Service</div>
<div class="abs field" style="left:301px;top:3233px;width:599px;height:101px;border-radius:30px">Messages</div>
<div class="abs btn" style="left:515px;top:3362px;width:170px;height:43px">SUBMIT</div>

<footer class="abs footer">
  <svg class="abs" style="left:0;top:-14px" width="1200" height="30" viewBox="0 0 1200 30" preserveAspectRatio="none"><path d="M0 16 C250 4 450 24 700 12 S1050 6 1200 14 V30 H0Z" fill="#ececec"/></svg>
  <div class="abs brand" style="left:116px;top:126px;font-size:22px">Marlow</div>
  <div class="abs" style="left:113px;top:202px;font-size:13px;color:#333">Copyright@2024 - All Rights Reserved</div>
  <div class="abs fcol" style="left:404px;top:111px"><h5>HOME CARE</h5><ul><li>Nurse Aide Care</li><li>Skilled Nursing</li><li>Lifestyle Aide</li><li>Hospice at Home</li><li>Bathing &amp; Meal Service.</li></ul></div>
  <div class="abs fcol" style="left:590px;top:111px"><h5>SENIOR LIVING</h5><ul><li>Long-Term Stay</li><li>Short-Term Stay</li><li>Rates</li></ul></div>
  <div class="abs fcol" style="left:768px;top:111px"><h5>ABOUT US</h5><ul><li>Our Mission</li><li>Ohana Talk</li><li>About Dana Marlow</li></ul></div>
  <div class="abs fcol" style="left:950px;top:111px"><h5>CONTACT US</h5>
    <ul>
      <li style="position:relative;padding-left:22px"><svg style="position:absolute;left:0;top:6px" width="10" height="14" viewBox="0 0 10 14"><path fill="#8fa383" d="M5 0a5 5 0 015 5c0 4-5 9-5 9S0 9 0 5a5 5 0 015-5z"/></svg>248 Pueo Lane,<br>Suite 310, Honolulu,<br>HI 96817.</li>
      <li style="position:relative;padding-left:22px;margin-top:6px"><svg style="position:absolute;left:0;top:7px" width="11" height="11" viewBox="0 0 24 24"><path fill="#8fa383" d="M6.6 10.8a15 15 0 006.6 6.6l2.2-2.2c.3-.3.7-.4 1-.2 1.1.4 2.3.6 3.6.6.6 0 1 .4 1 1V20c0 .6-.4 1-1 1A17 17 0 013 4c0-.6.4-1 1-1h3.5c.6 0 1 .4 1 1 0 1.3.2 2.5.6 3.6.1.3 0 .7-.2 1z"/></svg>808-555-0172</li>
    </ul>
  </div>
  <div class="abs btn" style="left:448px;top:286px;width:142px;height:38px;font-size:12px">LEARN</div>
  <div class="abs btn sand" style="left:601px;top:286px;width:150px;height:38px;font-size:12px">CAREGIVER JOBS</div>
</footer>

</body>
</html>
```